Redesign a Start-Up Dating Website

Website: https://morvelique.com.
Make sure the design has an island style theme.
I would like the 7 pages of my website to have a new and professional look. I want the same colors to remain, but I want a creative look for all the pages. This is a dating website that is in the startup stage. So, I want to give my entire website a custom makeover. I want something that will stand out from the other dating sites. Something that will attract more people to want to use my services, and hopefully get new members.
Target Market(s)
Dating
Industry/Entity Type
Dating
Coding
Coded - Design and coding required
Number of Pages Required
5+ page
Font styles to use
Other font styles liked:
- Decorative, San Serif
Requirements
Must have
- The design must have the original colors and a stylish font to go along. The design must be creative, welcoming, and professional. I would like an island style theme for the website. This is a dating website so make sure that the design is tailored to that aspect.
Nice to have
- It would be nice to have a decorative font and a professional style on all the pages. Make sure the design will be mobile responsive and friendly for all the pages on the website.
Should not have
- The design should not be bland and uncreative.

```html
<!DOCTYPE html>
<html lang="en">
<head>
<meta charset="utf-8">
<title>Morvelique – Online Dating</title>
<link href="https://fonts.googleapis.com/css2?family=Open+Sans:wght@400;600;700&family=Roboto+Slab:wght@600;700&display=swap" rel="stylesheet">
<style>
:root{
  --teal:#5fb8a8;
  --teal-dark:#4a9f90;
  --teal-soft:#7cc7b9;
  --orange:#f5a00f;
  --ink:#333a3f;
  --muted:#7b8287;
  --line:#e2e5e6;
  --footer:#eeeeee;
  --bottom:#3a3d40;
  --white:#ffffff;
}
*{box-sizing:border-box;margin:0;padding:0}
html,body{width:1200px;height:2676px;overflow:hidden;background:var(--white)}
body{font-family:"Open Sans",Arial,sans-serif;color:var(--ink);position:relative}
.abs{position:absolute}

/* top bar & header */
.account-bar{top:0;left:0;width:1200px;height:26px;border-bottom:1px solid var(--line)}
.account-bar .btns{position:absolute;right:30px;top:4px;display:flex;gap:6px}
.btn-mini{background:var(--orange);color:#fff;font-size:10px;font-weight:600;padding:3px 12px;border-radius:2px}
.site-header{top:26px;left:0;width:1200px;height:94px}
.brand{display:flex;align-items:center}
.brand .name{font-size:30px;font-weight:700;color:var(--ink)}
.site-header .brand{position:absolute;left:40px;top:24px}
.main-nav{position:absolute;right:32px;top:34px;display:flex;gap:40px;font-size:15px;font-weight:600;color:var(--ink)}
.main-nav .active{color:var(--orange);border-bottom:2px solid var(--orange);padding-bottom:4px}

/* hero */
.hero{top:128px;left:32px;width:1136px;height:444px;background:linear-gradient(100deg,#6a4a3a 0%,#b07a52 35%,#f1c48a 62%,#fbe7c4 100%)}
.hero-text{position:absolute;right:60px;top:146px;text-align:center;width:580px}
.hero-text h1{font-family:"Roboto Slab",Georgia,serif;font-size:32px;color:#fff;font-weight:700;text-shadow:0 2px 4px rgba(0,0,0,.3)}
.hero-text p{font-family:"Roboto Slab",Georgia,serif;font-size:21px;color:var(--orange);margin-top:10px;font-weight:600}
.hero-text .cta{display:inline-block;margin-top:26px;background:var(--orange);color:#fff;font-size:13px;font-weight:700;padding:12px 28px;border-radius:3px}
.hero .arrow{position:absolute;top:205px;width:34px;height:40px;background:rgba(0,0,0,.25)}
.slider-dots{top:580px;left:0;width:1200px;display:flex;justify-content:center;gap:7px}
.slider-dots span{width:10px;height:10px;border-radius:50%;border:2px solid var(--teal)}
.slider-dots span.on{background:var(--teal)}

/* welcome */
.welcome{top:666px;left:0;width:1200px;text-align:center}
.section-title{font-size:30px;font-weight:700;color:var(--ink)}
.welcome .lead{width:680px;margin:16px auto 0;font-size:13px;line-height:1.7;color:var(--muted)}
.features{display:flex;justify-content:center;gap:120px;margin-top:50px}
.feature{width:220px}
.feature .icon{width:84px;height:84px;border-radius:50%;border:3px solid var(--orange);margin:0 auto;display:flex;align-items:center;justify-content:center}
.feature h3{font-size:15px;font-weight:700;margin-top:18px}
.feature p{font-size:12px;color:var(--muted);line-height:1.6;margin-top:8px}

/* recent members */
.members-band{top:1270px;left:0;width:1200px;height:226px;background:var(--teal-soft)}
.members-panel{position:absolute;left:32px;top:16px;width:1136px;height:194px;background:#fff}
.members-panel .bar{height:36px;background:var(--teal);color:#fff;font-size:17px;font-weight:700;padding:7px 24px}
.member-row{position:absolute;top:52px;left:96px;display:flex;gap:58px}
.member{width:140px;text-align:center}
.member .photo{width:110px;height:100px;margin:0 auto}
.member .name{font-size:12px;margin-top:8px;color:var(--orange);font-weight:600;white-space:nowrap}
.member .name b{color:var(--ink);font-weight:600}
.member .loc{font-size:12px;color:var(--ink)}
.members-panel .nav-arrow{position:absolute;top:90px;font-size:28px;color:var(--muted)}

/* cta band */
.cta-band{top:1552px;left:0;width:1200px;height:320px;background:linear-gradient(180deg,var(--teal-soft),var(--teal));text-align:center;color:#fff}
.cta-band h2{font-family:"Roboto Slab",Georgia,serif;font-size:32px;margin-top:60px}
.cta-band .sub{font-size:12px;font-weight:600;margin-top:10px}
.cta-band h3{font-size:24px;font-weight:700;margin-top:18px}
.cta-band .cta{display:inline-block;margin-top:34px;background:var(--orange);color:#fff;font-size:13px;font-weight:700;padding:14px 34px;border-radius:3px}

/* stories & search */
.stories{top:2004px;left:60px;width:480px}
.block-title{font-size:24px;font-weight:700;padding-bottom:10px;border-bottom:1px solid var(--line)}
.story{display:flex;gap:16px;margin-top:22px}
.story .thumb{width:92px;height:80px;flex:none}
.story h4{font-size:15px;font-weight:600}
.story p{font-size:12px;color:var(--muted);line-height:1.5;margin-top:6px}
.pager{display:flex;gap:6px;margin-top:24px}
.pager span{width:22px;height:22px;border-radius:50%;background:var(--orange);color:#fff;font-size:12px;text-align:center;line-height:22px}
.search{top:2004px;left:600px;width:540px}
.search-form{border:1px solid var(--line);padding:20px;margin-top:16px;font-size:13px}
.row{display:flex;align-items:center;gap:10px;margin-bottom:14px}
.row label{width:56px;font-weight:600}
.select{height:28px;border:1px solid #d3d7d9;background:#f7f8f8;border-radius:2px;font-size:12px;color:var(--muted);padding:5px 10px;position:relative}
.select::after{content:"";position:absolute;right:10px;top:11px;border:4px solid transparent;border-top-color:var(--muted)}
.search-btn{background:var(--orange);color:#fff;font-weight:700;font-size:14px;text-align:center;padding:12px;margin-top:6px;border-radius:2px}

/* footer */
.site-footer{top:2448px;left:0;width:1200px;height:172px;background:var(--footer);text-align:center}
.site-footer .brand{justify-content:center;margin-top:42px}
.site-footer .brand .name{font-size:26px}
.footer-nav{display:flex;justify-content:center;gap:18px;margin-top:22px;font-size:13px;color:var(--muted)}
.bottom-bar{top:2620px;left:0;width:1200px;height:56px;background:var(--bottom);color:#bfc3c5;font-size:11px}
.bottom-bar .copy{position:absolute;left:40px;top:21px}
.social{position:absolute;right:40px;top:16px;display:flex;gap:8px}
.social span{width:24px;height:24px;border:1px solid #8a8f92;border-radius:3px}
</style>
</head>
<body>

<div class="abs account-bar">
  <div class="btns"><span class="btn-mini">Login</span><span class="btn-mini">Register</span></div>
</div>

<header class="abs site-header">
  <div class="brand"><span class="name">Morvelique</span></div>
  <nav class="main-nav">
    <span class="active">Home</span><span>Search</span><span>Members</span><span>Extras</span><span>About</span><span>Premium</span><span>Contact</span>
  </nav>
</header>

<section class="abs hero" role="img" aria-label="Couple embracing at sunset by the sea">
  <span class="arrow" style="left:0"></span>
  <span class="arrow" style="right:0"></span>
  <div class="hero-text">
    <h1>Let's Find Your Perfect Match Today</h1>
    <p>Online Dating Made Easy On morvelique.com</p>
    <span class="cta">Begin With Free Signup</span>
  </div>
</section>
<div class="abs slider-dots"><span class="on"></span><span></span><span></span></div>

<section class="abs welcome">
  <h2 class="section-title">Welcome To Morvelique</h2>
  <p class="lead">Morvelique aims to provide a straightforward, easy-to-use online dating service. I wasn't over-complicating things or collect the amount of people you can talk to with algorithms. I know that sometimes, opposites attract and sparks can fly with the last person you thought you'd be interested in so I won't hide anybody from you.</p>
  <div class="features">
    <div class="feature">
      <div class="icon"><svg width="40" height="40" viewBox="0 0 40 40" fill="none" stroke="#f5a00f" stroke-width="3"><circle cx="20" cy="14" r="7"/><path d="M6 36c2-9 8-12 14-12s12 3 14 12"/></svg></div>
      <h3>Create Your Profile</h3>
      <p>Let people know all about you, the good and the quirky, share the world your true colors and find someone with the same unique qualities as you.</p>
    </div>
    <div class="feature">
      <div class="icon"><svg width="40" height="40" viewBox="0 0 40 40" fill="none" stroke="#f5a00f" stroke-width="3"><path d="M20 34S5 25 5 14a8 8 0 0 1 15-4 8 8 0 0 1 15 4c0 11-15 20-15 20z"/></svg></div>
      <h3>Find Matches</h3>
      <p>Browse other users and feel the excitement of getting your first message and getting to know potential dates in a safe and fun environment.</p>
    </div>
    <div class="feature">
      <div class="icon"><svg width="40" height="40" viewBox="0 0 40 40" fill="none" stroke="#f5a00f" stroke-width="3"><path d="M6 8h28v18H16l-8 6v-6H6z"/></svg></div>
      <h3>Start Dating</h3>
      <p>Once you've found your potential soulmate, it's time to meet up and say 'Hello' to the start of your journey together.</p>
    </div>
  </div>
</section>

<section class="abs members-band">
  <div class="members-panel">
    <div class="bar">Recently Joined New Users</div>
    <span class="nav-arrow" style="left:16px">‹</span>
    <span class="nav-arrow" style="right:16px">›</span>
    <div class="member-row">
      <div class="member"><div class="photo" role="img" aria-label="Member photo" style="background:linear-gradient(160deg,#d9b48f,#8b6648)"></div><div class="name">Vivian Marlow <b>, 21</b></div><div class="loc">New York</div></div>
      <div class="member"><div class="photo" role="img" aria-label="Member photo" style="background:linear-gradient(160deg,#7a8794,#2f3a44)"></div><div class="name">Lucas Sheridan <b>, 25</b></div><div class="loc">Alaska</div></div>
      <div class="member"><div class="photo" role="img" aria-label="Member photo" style="background:linear-gradient(160deg,#c9a27c,#6d4a33)"></div><div class="name">Leona Brink <b>, 24</b></div><div class="loc">Florida</div></div>
      <div class="member"><div class="photo" role="img" aria-label="Member photo" style="background:linear-gradient(160deg,#a89a8a,#5a4c40)"></div><div class="name">Will Fenton <b>, 27</b></div><div class="loc">California</div></div>
      <div class="member"><div class="photo" role="img" aria-label="Member photo" style="background:linear-gradient(160deg,#b6c4cc,#5f6e78)"></div><div class="name">David Langston <b>, 29</b></div><div class="loc">Texas</div></div>
    </div>
  </div>
</section>

<section class="abs cta-band">
  <h2>Dating is EASY with Morvelique</h2>
  <p class="sub">Sign Up For A 30 Days Free Trial. Enjoy All The Benefits Morvelique Has To Offer With A Full Membership.</p>
  <h3>Join This Community Of 1 Morvelique Members</h3>
  <span class="cta">Start Morvelique With Free Signup</span>
</section>

<section class="abs stories">
  <h2 class="block-title">Stories</h2>
  <div class="story">
    <div class="thumb" role="img" aria-label="Couple photo" style="background:linear-gradient(160deg,#9fb4c0,#4b5f6b)"></div>
    <div><h4>This couple met on Listboard</h4><p>I met my wife on Listboard in 2008. I had been living outside of a small town and moved...</p></div>
  </div>
  <div class="story">
    <div class="thumb" role="img" aria-label="Couple photo" style="background:linear-gradient(160deg,#d6a47e,#7a4f36)"></div>
    <div><h4>Believe it or not, that...</h4><p>We met online fifteen years back in the old days of dial-up modems. Had a number...</p></div>
  </div>
  <div class="pager"><span>‹</span><span>›</span></div>
</section>

<section class="abs search">
  <h2 class="block-title">Search For Your Partner Now !</h2>
  <div class="search-form">
    <div class="row"><label>I am</label><div class="select" style="width:140px">Man</div><label style="width:76px;margin-left:20px">Seeking a</label><div class="select" style="width:140px">Woman</div></div>
    <div class="row"><label>Age</label><div class="select" style="width:140px">18</div><label style="width:76px;margin-left:20px">Age</label><div class="select" style="width:140px">99</div></div>
    <div class="row" style="margin-bottom:6px"><label style="width:auto">Choose The Country</label></div>
    <div class="row"><div class="select" style="width:260px">Any Country</div></div>
    <div class="search-btn">START SEARCH</div>
  </div>
</section>

<footer class="abs site-footer">
  <div class="brand"><span class="name">Morvelique</span></div>
  <nav class="footer-nav"><span>Home</span><span>|</span><span>Search</span><span>|</span><span>Members</span><span>|</span><span>Extras</span><span>|</span><span>About</span><span>|</span><span>Premium</span><span>|</span><span>Contact</span></nav>
</footer>
<div class="abs bottom-bar">
  <span class="copy">Copyright © 2017 Morvelique - All Rights Reserved</span>
  <div class="social"><span></span><span></span><span></span></div>
</div>

</body>
</html>
```